BOLD & MINIMALIST DESIGN NEEDED

We want a very bold but minimalistic business card design that is impactful and utilizes both sides of the business card. Our current logo is included for your use.

We want bold fonts and good use of negative space. We don't want the logo to overpower the design.

Target Market(s)

Professionals who are building new commercial buildings.

Industry/Entity Type

Construction

Contact Information for Business Card

Name, Title, email, office phone, cell phone, website

Font styles to use
Serif
Sans Serif

Requirements
Must have
• Bold design!

```html
<!DOCTYPE html>
<html lang="en">
<head>
<meta charset="utf-8">
<title>Ridgeline Design + Build – Business Card</title>
<link href="https://fonts.googleapis.com/css2?family=Roboto:wght@400;500;700&display=swap" rel="stylesheet">
<style>
  :root {
    --stage: #e2e2e2;
    --paper: #f4f4f4;
    --ink: #111111;
    --text: #222222;
    --green: #7fba27;
    --green-light: #b2d87a;
    --green-glow: #a6d165;
  }
  * { box-sizing: border-box; margin: 0; padding: 0; }
  html, body { width: 1200px; height: 1040px; overflow: hidden; }
  body {
    background: var(--stage);
    font-family: "Roboto", Arial, sans-serif;
    position: relative;
  }
  .card {
    position: absolute;
    left: 280px;
    width: 640px;
    height: 366px;
    border-radius: 16px;
    overflow: hidden;
  }
  /* Front */
  .card-front { top: 130px; background: var(--paper); }
  .wordmark {
    position: absolute;
    left: 40px;
    top: 148px;
    width: 250px;
    display: flex;
    align-items: center;
    gap: 10px;
    justify-content: center;
  }
  .wordmark-square {
    width: 22px; height: 22px;
    background: var(--green);
    flex: none;
  }
  .wordmark-name {
    font-weight: 700;
    font-size: 27px;
    line-height: 1;
    color: var(--ink);
    letter-spacing: 0.5px;
  }
  .wordmark-name small {
    display: block;
    font-size: 13px;
    letter-spacing: 5px;
    margin-top: 6px;
    font-weight: 700;
  }
  .divider {
    position: absolute;
    left: 321px; top: 102px;
    width: 1px; height: 180px;
    background: #c9c9c9;
  }
  .contact {
    position: absolute;
    left: 340px; top: 105px;
    color: var(--text);
  }
  .contact-name {
    font-weight: 700;
    font-size: 26px;
    line-height: 1;
    color: var(--ink);
  }
  .contact-title {
    font-size: 16px;
    color: var(--green);
    margin-top: 4px;
  }
  .contact-address {
    font-size: 16px;
    line-height: 20px;
    margin-top: 14px;
  }
  .contact-lines { list-style: none; margin-top: 12px; }
  .contact-lines li {
    font-size: 16px;
    line-height: 20px;
    display: flex;
    align-items: center;
    gap: 8px;
  }
  .contact-lines svg { width: 14px; height: 14px; flex: none; }
  .band {
    position: absolute;
    left: 0; bottom: 0;
    width: 100%; height: 18px;
  }
  /* Back */
  .card-back {
    top: 570px;
    background: radial-gradient(ellipse 60% 70% at 50% 48%, var(--green-glow) 0%, var(--green) 100%);
  }
  .back-wordmark {
    position: absolute;
    left: 0; right: 0; top: 140px;
    display: flex;
    justify-content: center;
    align-items: center;
    gap: 14px;
  }
  .back-wordmark .wordmark-square { width: 34px; height: 34px; background: var(--ink); }
  .back-wordmark .wordmark-name { font-size: 44px; }
  .back-web {
    position: absolute;
    left: 0; right: 0; top: 312px;
    text-align: center;
    font-size: 15px;
    color: #1e1e1e;
  }
</style>
</head>
<body>

<section class="card card-front">
  <div class="wordmark">
    <span class="wordmark-square"></span>
    <span class="wordmark-name">RIDGELINE<small>DESIGN + BUILD</small></span>
  </div>
  <div class="divider"></div>
  <div class="contact">
    <h1 class="contact-name">OWEN CARTER</h1>
    <p class="contact-title">President</p>
    <p class="contact-address">4120 Larkspur Avenue<br>Maple Grove, NY 11020</p>
    <ul class="contact-lines">
      <li>
        <svg viewBox="0 0 24 24"><path fill="#111" d="M6.6 10.8a15 15 0 0 0 6.6 6.6l2.2-2.2c.3-.3.7-.4 1-.2 1.1.4 2.3.6 3.6.6.6 0 1 .4 1 1V20c0 .6-.4 1-1 1A17 17 0 0 1 3 4c0-.6.4-1 1-1h3.5c.6 0 1 .4 1 1 0 1.3.2 2.5.6 3.6.1.3 0 .7-.2 1z"/></svg>
        (555) 0142-7781
      </li>
      <li>
        <svg viewBox="0 0 24 24"><rect x="2" y="5" width="20" height="14" fill="#111"/><path d="M3 6l9 7 9-7" fill="none" stroke="#f4f4f4" stroke-width="2"/></svg>
        info@ridgelinebuild.com
      </li>
      <li>
        <svg viewBox="0 0 24 24"><circle cx="12" cy="12" r="10" fill="#111"/><path d="M2 12h20M12 2c3 3 3 17 0 20M12 2c-3 3-3 17 0 20" fill="none" stroke="#f4f4f4" stroke-width="1.5"/></svg>
        www.ridgelinebuild.com
      </li>
    </ul>
  </div>
  <svg class="band" viewBox="0 0 640 18" preserveAspectRatio="none">
    <defs>
      <linearGradient id="bandGreen" x1="0" x2="1">
        <stop offset="0" stop-color="#7fba27"/>
        <stop offset="1" stop-color="#b2d87a"/>
      </linearGradient>
    </defs>
    <polygon points="0,0 416,0 411,18 0,18" fill="#111"/>
    <polygon points="420,0 640,0 640,18 415,18" fill="url(#bandGreen)"/>
  </svg>
</section>

<section class="card card-back">
  <div class="back-wordmark">
    <span class="wordmark-square"></span>
    <span class="wordmark-name">RIDGELINE</span>
  </div>
  <p class="back-web">www.ridgelinebuild.com</p>
</section>

</body>
</html>
```